Dental office stationary (letterhead, envelopes), business cards, presentation folders

Nothing too dental outside of the logo. I will need all stationary, presentation folders, business cards. Would prefer to stay in the colors of the logo

Gordon Patel, DDS
Bright Haven Dental Implant Center
555-318-2790
info@brighthavendental.example
4817 NW Maple Crest Rd Unit B
Harbor Glen, ST 00000

Also need appointment date and time
And cancellation policy
I want it to say “kindly ask for
A 48hr cancellation policy to avoid incurring a cancellation fee”

Industry/Entity Type

Dental

Colors
0054AA
0677BA
7BADD7
CADEEF
E8F1F8

Requirements
Must have
• Name of your office, name of doctor, address, phone number
Should not have
• Too much tooth/dental. Only the tooth in logo

```html
<!DOCTYPE html>
<html lang="en">
<head>
<meta charset="utf-8">
<title>Bright Haven Dental Implant Center – Stationery</title>
<link rel="stylesheet" href="https://fonts.googleapis.com/css2?family=Montserrat:wght@400;500;600;700&display=swap">
<style>
:root{
  --navy:#0054AA;
  --blue:#0677BA;
  --sky:#7BADD7;
  --pale:#CADEEF;
  --mist:#E8F1F8;
  --ink:#1f1f1f;
  --stage:#b9b8ba;
  --paper:#ffffff;
  --grad:linear-gradient(135deg,#2a62b4 0%,#2d7cc4 55%,#3aa3da 100%);
}
*{box-sizing:border-box;margin:0;padding:0}
html,body{width:1200px;height:627px;overflow:hidden}
body{background:var(--stage);font-family:"Montserrat",sans-serif;color:var(--ink);position:relative}
.piece{position:absolute;background:var(--paper);box-shadow:0 2px 6px rgba(0,0,0,.18)}
.brand{font-family:"Montserrat",sans-serif;font-weight:600;color:var(--blue);line-height:1.05;letter-spacing:.02em;white-space:nowrap}
.brand small{display:block;font-size:.42em;letter-spacing:.18em;text-transform:uppercase;margin-top:.25em}
.divider{position:absolute;width:1px;background:var(--blue)}
.contact{position:absolute;line-height:1.38;font-style:normal;white-space:nowrap}
.contact .org{color:var(--blue)}
.contact .gap{height:.6em}
.contact .row{display:flex;align-items:center;gap:3px}
.contact svg{width:.95em;height:.95em;fill:var(--blue);flex:none}

/* letterhead */
.letterhead{left:74px;top:76px;width:349px;height:494px}
.letterhead .brand{position:absolute;left:17px;top:30px;font-size:17px}
.letterhead .divider{left:205px;top:21px;height:52px}
.letterhead .contact{left:223px;top:22px;font-size:6.5px}
.watermark{position:absolute;left:104px;top:136px;width:172px;height:172px;border-radius:50%;background:var(--mist);opacity:.7}
.letter{position:absolute;left:17px;top:113px;width:314px;font-size:7px;line-height:1.12;text-align:justify}
.letter p{margin-bottom:7.5px}
.letter .salute{font-size:8.5px;font-weight:600;margin:9px 0 9px}
.letter .block{text-align:left}
.signature{position:absolute;left:17px;top:400px;width:74px;height:18px;background:linear-gradient(90deg,#d9d9d9,#ececec)}

/* folder */
.folder{left:495px;width:330px;height:220px;display:flex;overflow:hidden}
.folder .half{position:relative;width:50%;height:100%}
.folder-out{top:80px}
.folder-out .front-left{background:var(--paper)}
.folder-out .front-left .brand{position:absolute;left:14px;top:36px;font-size:17px}
.folder-out .front-left .contact{left:14px;bottom:16px;font-size:5.6px}
.folder-out .front-right{background:var(--grad)}
.cover-disc{position:absolute;left:50%;top:50%;width:96px;height:96px;margin:-48px 0 0 -48px;border-radius:50%;background:var(--paper)}
.folder-in{top:320px}
.folder-in .inner-left{background:linear-gradient(90deg,#f4f4f4,#e2e2e2)}
.folder-in .inner-right{background:linear-gradient(90deg,#e4e4e4,#f6f6f6)}
.pocket{position:absolute;left:0;right:0;bottom:0;height:72px;background:var(--grad);border-radius:26px 0 0 0}
.inner-left .pocket{border-radius:0 26px 0 0}
.sheet{position:absolute;left:18px;top:12px;width:128px;height:170px;background:var(--paper);box-shadow:0 1px 3px rgba(0,0,0,.2)}
.sheet .brand{position:absolute;left:8px;top:14px;font-size:7px}
.sheet .bars{position:absolute;left:8px;right:8px;top:48px}
.sheet .bars i{display:block;height:2px;background:#cfcfcf;margin-bottom:3px}

/* envelopes */
.envelope{left:892px;width:236px}
.env-back{top:76px;height:103px}
.flap{position:absolute;left:0;right:0;top:0;height:37px;background:linear-gradient(90deg,#2555a8,#2a60b4);border-radius:0 0 12px 12px}
.flap-disc{position:absolute;left:50%;top:8px;width:21px;height:21px;margin-left:-10px;border-radius:50%;border:3px solid var(--paper)}
.env-front{top:195px;height:102px}
.env-front .brand{position:absolute;left:9px;top:13px;font-size:7px}
.env-front .divider{left:70px;top:9px;height:25px}
.env-front .contact{left:78px;top:10px;font-size:4.2px}

/* business cards */
.card{left:913px;width:215px;border-radius:9px}
.card-front{top:313px;height:124px;background:var(--grad);display:flex;align-items:center;justify-content:center}
.card-front .brand{color:var(--paper);font-size:24px;text-align:center;font-weight:500}
.card-back{top:448px;height:123px}
.card-back .brand{position:absolute;left:11px;top:47px;font-size:11px}
.card-back .divider{left:111px;top:26px;height:72px}
.card-back .contact{left:118px;top:24px;font-size:4.9px}
.card-back .title{font-size:8.3px;font-weight:700;color:var(--blue);margin-bottom:1px}
</style>
</head>
<body>

<!-- Letterhead -->
<section class="piece letterhead">
  <div class="watermark"></div>
  <div class="brand">Bright Haven<small>Dental Implant Center</small></div>
  <div class="divider"></div>
  <address class="contact">
    <div class="org">Bright Haven Dental Implant Center</div>
    <div>4817 NW Maple Crest Rd Unit B</div>
    <div>Harbor Glen, ST 00000</div>
    <div class="gap"></div>
    <div class="row"><svg viewBox="0 0 10 10"><path d="M2 1h2l1 2-1 1q1 2 2 2l1-1 2 1v2q-1 1-2 1Q1 9 1 3q0-1 1-2z"/></svg>555-318-2790</div>
    <div class="row"><svg viewBox="0 0 10 10"><path d="M1 2h8v6H1zM1.6 2.6v.4L5 5.4 8.4 3v-.4z"/></svg>info@brighthavendental.example</div>
    <div class="row"><svg viewBox="0 0 10 10"><circle cx="5" cy="5" r="4"/></svg>www.brighthavendental.example</div>
  </address>
  <div class="letter">
    <p class="block">January-03-2020</p>
    <p class="block">Mr, John Doe<br>President</p>
    <p class="block">Link Corpration<br>123 Street Name, Suite# 10<br>City, State, 120023</p>
    <p class="salute">Dear Mr, John</p>
    <p>Lorem ipsum dolor sit amet, consectetur adipiscing elit, sed do eiusmod tempor incididunt ut labore et dolore magna aliqua. Ut enim ad minim veniam, quis nostrud exercitation ullamco laboris nisi ut aliquip ex ea commodo consequat. Duis aute irure dolor in reprehenderit in voluptate velit esse cillum dolore eu fugiat nulla pariatur.</p>
    <p>Lorem ipsum dolor sit amet, consectetur adipiscing elit, sed do eiusmod tempor incididunt ut labore et dolore magna aliqua. Ut enim ad minim veniam, quis nostrud exercitation ullamco laboris nisi ut aliquip ex ea commodo consequat. Duis aute irure dolor in reprehenderit in voluptate velit esse cillum dolore eu fugiat nulla pariatur.</p>
    <p>Lorem ipsum dolor sit amet, consectetur adipiscing elit, sed do eiusmod tempor incididunt ut labore et dolore magna aliqua. Ut enim ad minim veniam, quis nostrud exercitation ullamco laboris nisi ut aliquip ex ea commodo consequat.</p>
    <p>Excepteur sint occaecat cupidatat non proident, sunt in culpa qui officia deserunt mollit anim id est laborum. re et dolore magnam aliquam quaerat voluptatem.</p>
    <p class="block" style="margin-top:14px">Regards</p>
  </div>
  <div class="signature" role="img" aria-label="Handwritten signature of the sender"></div>
</section>

<!-- Presentation folder, outside -->
<section class="piece folder folder-out">
  <div class="half front-left">
    <div class="brand">Bright Haven<small>Dental Implant Center</small></div>
    <address class="contact">
      <div class="org">Bright Haven Dental Implant Center</div>
      <div>4817 NW Maple Crest Rd Unit B Harbor Glen, ST 00000</div>
      <div>555-318-2790 · info@brighthavendental.example</div>
      <div>www.brighthavendental.example</div>
    </address>
  </div>
  <div class="half front-right"><div class="cover-disc"></div></div>
</section>

<!-- Presentation folder, inside -->
<section class="piece folder folder-in">
  <div class="half inner-left"><div class="pocket"></div></div>
  <div class="half inner-right">
    <div class="sheet">
      <div class="brand">Bright Haven<small>Dental Implant Center</small></div>
      <div class="bars"><i></i><i style="width:70%"></i><i></i><i></i><i style="width:85%"></i><i></i><i></i><i style="width:60%"></i><i></i><i></i><i style="width:75%"></i></div>
    </div>
    <div class="pocket"></div>
  </div>
</section>

<!-- Envelope back -->
<section class="piece envelope env-back">
  <div class="flap"><div class="flap-disc"></div></div>
</section>

<!-- Envelope front -->
<section class="piece envelope env-front">
  <div class="brand">Bright Haven<small>Dental Implant Center</small></div>
  <div class="divider"></div>
  <address class="contact">
    <div class="org">Bright Haven Dental Implant Center</div>
    <div>4817 NW Maple Crest Rd Unit B</div>
    <div>Harbor Glen, ST 00000</div>
  </address>
</section>

<!-- Business card front -->
<section class="piece card card-front">
  <div class="brand">Bright Haven<small>Dental Implant Center</small></div>
</section>

<!-- Business card back -->
<section class="piece card card-back">
  <div class="brand">Bright Haven<small>Dental Implant Center</small></div>
  <div class="divider"></div>
  <address class="contact">
    <div class="title">Name of Doctor</div>
    <div>Gordon Patel, DDS</div>
    <div>Bright Haven Dental Implant Center</div>
    <div class="gap"></div>
    <div>4817 NW Maple Crest Rd Unit B</div>
    <div>Harbor Glen, ST 00000</div>
    <div class="gap"></div>
    <div class="row"><svg viewBox="0 0 10 10"><path d="M2 1h2l1 2-1 1q1 2 2 2l1-1 2 1v2q-1 1-2 1Q1 9 1 3q0-1 1-2z"/></svg>555-318-2790</div>
    <div class="row"><svg viewBox="0 0 10 10"><path d="M1 2h8v6H1zM1.6 2.6v.4L5 5.4 8.4 3v-.4z"/></svg>info@brighthavendental.example</div>
    <div class="row"><svg viewBox="0 0 10 10"><circle cx="5" cy="5" r="4"/></svg>www.brighthavendental.example</div>
  </address>
</section>

</body>
</html>
```